Copperleaf Roofing Business Card

This is my current business card. But I’d like to make some changes. Somewhere on the card I’d like to list some of the services we offer. Maybe on the back? But I’d still like to keep the red. White and black modern look.

-residential & commercial roofing
-Roof Repairs & Maintenance
-Storm Damage & Insurance Claims specialist
-Christmas Lights and permanent Christmas lights
Fencing. Windows. Gutters. Siding. Sheetrock, painting.

```html
<!DOCTYPE html>
<html lang="en">
<head>
<meta charset="utf-8">
<title>Copperleaf Roofing Business Card</title>
<link rel="stylesheet" href="https://fonts.googleapis.com/css2?family=Montserrat:wght@400;500;800&family=Roboto+Condensed:wght@400;700&display=swap">
<style>
  :root {
    --red: #e0101a;
    --red-deep: #8c0008;
    --black: #0b0b0b;
    --white: #ffffff;
    --ink: #161616;
    --rule: #9a9a9a;
    --backdrop: #2a2a2a;
  }
  * { box-sizing: border-box; margin: 0; padding: 0; }
  html, body { width: 1200px; height: 1108px; overflow: hidden; }
  body {
    background: var(--backdrop);
    position: relative;
    font-family: "Montserrat", sans-serif;
  }
  .card {
    position: absolute;
    top: 169px;
    width: 440px;
    height: 770px;
    border-radius: 26px;
    overflow: hidden;
  }
  /* Front */
  .card-front {
    left: 120px;
    background: var(--white);
    text-align: center;
    color: var(--ink);
  }
  .brand-dot {
    width: 150px; height: 150px;
    border-radius: 50%;
    background: var(--red);
    margin: 80px auto 0;
  }
  .brand-name {
    margin-top: 36px;
    font-family: "Montserrat", sans-serif;
    font-weight: 800;
    color: var(--red);
    font-size: 40px;
    line-height: 1.05;
    letter-spacing: 1px;
    text-transform: uppercase;
  }
  .brand-name .line-small { display: block; font-size: 27px; letter-spacing: 3px; }
  .person-name {
    margin-top: 72px;
    font-weight: 800;
    font-size: 34px;
    letter-spacing: 2px;
    text-transform: uppercase;
  }
  .person-name .first { color: var(--red); }
  .person-role {
    font-weight: 400;
    font-size: 26px;
    letter-spacing: 1px;
    margin-top: 2px;
  }
  .contact-icons {
    display: flex;
    align-items: center;
    justify-content: center;
    gap: 10px;
    margin: 18px 40px 0;
  }
  .contact-icons .rule { flex: 1; height: 1px; background: var(--rule); }
  .icon {
    width: 44px; height: 44px;
    border-radius: 8px;
    background: var(--red);
    display: flex; align-items: center; justify-content: center;
  }
  .contact-list { margin-top: 22px; list-style: none; font-size: 24px; line-height: 1.45; font-weight: 500; }
  .contact-list .web-accent { color: var(--red); font-weight: 800; }

  /* Back */
  .card-back {
    left: 640px;
    background: linear-gradient(160deg, var(--red) 0%, var(--red-deep) 100%);
  }
  .back-top {
    position: absolute; inset: 0 0 auto 0;
    height: 470px;
  }
  .back-top svg { position: absolute; inset: 0; }
  .services {
    position: relative;
    padding: 54px 34px 0;
    text-align: center;
    font-family: "Roboto Condensed", sans-serif;
  }
  .services-main {
    list-style: none;
    color: var(--white);
    font-weight: 700;
    font-size: 25px;
    line-height: 1.3;
  }
  .services-main li + li { margin-top: 4px; }
  .services-rule { height: 1px; background: #555; margin: 20px 10px 16px; }
  .services-extra {
    color: var(--red);
    font-weight: 400;
    font-size: 21px;
    line-height: 1.45;
    text-transform: uppercase;
  }
  .mascot-art {
    position: absolute;
    left: 50px; right: 50px;
    top: 430px; bottom: 40px;
    border-radius: 40% 40% 46% 46%;
    background: radial-gradient(ellipse at 50% 40%, #1a0002 0%, #3a0004 55%, rgba(90,0,6,0) 75%);
  }
</style>
</head>
<body>

<section class="card card-front" aria-label="Business card front">
  <div class="brand-dot"></div>
  <h1 class="brand-name">Copperleaf<span class="line-small">Roofing Co.</span></h1>
  <p class="person-name"><span class="first">Dana</span> Mercer</p>
  <p class="person-role">OWNER</p>
  <div class="contact-icons">
    <span class="rule"></span>
    <span class="icon"><svg width="26" height="26" viewBox="0 0 24 24" fill="#fff"><path d="M6.6 10.8a15.1 15.1 0 0 0 6.6 6.6l2.2-2.2c.3-.3.7-.4 1-.2 1.1.4 2.3.6 3.6.6.6 0 1 .4 1 1V20c0 .6-.4 1-1 1A17 17 0 0 1 3 4c0-.6.4-1 1-1h3.5c.6 0 1 .4 1 1 0 1.3.2 2.5.6 3.6.1.3 0 .7-.2 1z"/></svg></span>
    <span class="icon"><svg width="26" height="26" viewBox="0 0 24 24" fill="none" stroke="#fff" stroke-width="2"><rect x="3" y="5" width="18" height="14" rx="1"/><path d="M3 6l9 7 9-7"/></svg></span>
    <span class="icon"><svg width="26" height="26" viewBox="0 0 24 24" fill="none" stroke="#fff" stroke-width="2"><circle cx="12" cy="12" r="9"/><path d="M3 12h18M12 3c3 3 3 15 0 18M12 3c-3 3-3 15 0 18"/></svg></span>
    <span class="rule"></span>
  </div>
  <ul class="contact-list">
    <li>555-014-2288</li>
    <li>dana@copperleafroofing.co</li>
    <li>www.<span class="web-accent">copperleafroofing</span>.co</li>
  </ul>
</section>

<section class="card card-back" aria-label="Business card back">
  <div class="mascot-art" role="img" aria-label="Large dark mascot illustration on red"></div>
  <div class="back-top">
    <svg width="440" height="470" viewBox="0 0 440 470" preserveAspectRatio="none">
      <path d="M0 0H440V300C440 470 0 470 0 300Z" fill="var(--black)"/>
    </svg>
    <div class="services">
      <ul class="services-main">
        <li>Residential &amp; Commercial Roofing</li>
        <li>Roof Repairs &amp; Maintenance</li>
        <li>Storm Damage &amp; Insurance<br>Claims Specialist</li>
        <li>Christmas Lights and Permanent<br>Christmas Lights</li>
      </ul>
      <div class="services-rule"></div>
      <p class="services-extra">Fencing • Windows • Gutters • Siding<br>Sheetrock • Painting</p>
    </div>
  </div>
</section>

</body>
</html>
```